Flat Belly Design Graphics for Social

I want to create 9 social media graphics (new Instagram size 4:5 (1080 x 1350 pixels) focusing on our Flat Belly Graphics, using the pics attached. Use the attached pics, NO RANDOM STOCK PHOTOGRAPHY. For the color scheme of the graphics, the color palette is attached. YOU MUST POST ALL 9 GRAPHICS IN ONE ENTRY.
Using the 3 titles below, create one set of graphics. 1) with all text, then for the others, use the pictures as detailed below in IMPORTANT:
1. Ten-Week Bright Morning Reboot
2. The Quick Garden Kitchen Menu Guide
3. Studio Habits for Lasting Energy Past Midlife - Zero Gym Needed
IMPORTANT:
Only use RK Pic 1 and RK Pic 2 with the title, Ten-Week Bright Morning Reboot
Only use meal plan1 and meal plan2 pics with the title, Quick Garden Kitchen Menu Guide
Only use studio habits 1 and studio habits 2 pics with the title, Studio Habits for Lasting Energy Past Midlife - Zero Gym Needed
women over 40

```html
<!DOCTYPE html>
<html lang="en">
<head>
<meta charset="utf-8">
<title>Ten-Week Bright Morning Reboot – Social Set</title>
<link rel="stylesheet" href="https://fonts.googleapis.com/css2?family=Lexend:wght@500;600;700;800&family=Great+Vibes&family=Oswald:wght@600;700&family=Poppins:wght@600;700&display=swap">
<style>
  :root {
    --stage: #232323;
    --card: #fbe6ec;
    --panel: #fdedf1;
    --pink: #ef86ab;
    --pink-soft: #f6bfd2;
    --pink-line: #eb9ab6;
    --pink-deep: #d95a8c;
    --green: #145a4e;
    --white: #ffffff;
  }
  * { margin: 0; padding: 0; box-sizing: border-box; }
  html, body { width: 960px; height: 1200px; overflow: hidden; background: var(--stage); }
  .stage { position: relative; width: 960px; height: 1200px; background: var(--stage); }

  .card { position: absolute; width: 231px; height: 289px; background: var(--card); }
  .col-1 { left: 110px; } .col-2 { left: 363px; } .col-3 { left: 616px; }
  .row-1 { top: 132px; } .row-2 { top: 452px; } .row-3 { top: 772px; }

  .frame {
    position: absolute; left: 8px; top: 8px; width: 215px; height: 273px;
    border: 1px solid var(--pink-line); border-radius: 24px; overflow: hidden;
    background: var(--panel);
  }
  .halo { position: absolute; border-radius: 50%; background: var(--pink-soft); opacity: .55; }
  .halo::after { content: ""; position: absolute; inset: -14px; border-radius: 50%; background: var(--pink-soft); opacity: .35; }
  .halo-tl { left: -16px; top: -16px; width: 70px; height: 70px; }
  .halo-br { right: -14px; bottom: -14px; width: 70px; height: 70px; }

  .t { position: absolute; left: 0; right: 0; text-align: center; line-height: 1; white-space: nowrap; }
  .t-left { left: 9px; right: auto; text-align: left; }
  .t-right { left: auto; text-align: right; }
  .wide { font-family: "Lexend", sans-serif; font-weight: 800; color: var(--green); letter-spacing: .02em; }
  .lex { font-family: "Lexend", sans-serif; }
  .script { font-family: "Great Vibes", cursive; color: var(--pink); font-weight: 400; }
  .cond { font-family: "Oswald", sans-serif; font-weight: 700; }
  .round { font-family: "Poppins", sans-serif; font-weight: 700; }
  .pink { color: var(--pink); }
  .green { color: var(--green); }

  .pill {
    position: absolute; background: var(--pink); color: var(--white);
    border-radius: 20px; display: flex; align-items: center; justify-content: center;
    font-family: "Lexend", sans-serif; font-weight: 700; letter-spacing: .03em; white-space: nowrap;
  }

  .photo { position: absolute; }
  .photo-person { border-radius: 40px 40px 6px 6px; background: linear-gradient(180deg, #3a2a26 0%, #a0705c 28%, #f1efee 48%, #e9e4e4 66%, #1c1c1e 82%); }
  .photo-food { background: linear-gradient(135deg, #e9b7a6 0%, #6b4a34 35%, #b94a3a 55%, #5c7d3a 75%, #5a3c2a 100%); }
  .photo-friends { background: linear-gradient(120deg, #3b2420 0%, #b98262 35%, #f2ede9 55%, #c9906c 75%, #2a1a17 100%); }
  .fade-bottom::after { content: ""; position: absolute; left: 0; right: 0; bottom: 0; height: 45%; background: linear-gradient(180deg, rgba(253,237,241,0), var(--panel)); }
  .fade-mid::after { content: ""; position: absolute; left: 0; right: 0; top: 26%; height: 48%; background: linear-gradient(180deg, rgba(253,237,241,0), rgba(253,237,241,.95) 25%, rgba(253,237,241,.95) 75%, rgba(253,237,241,0)); }

  .bubble {
    position: absolute; left: 11px; top: 16px; width: 189px; height: 63px;
    background: var(--pink); border-radius: 10px; color: var(--white);
    font-family: "Lexend", sans-serif; font-weight: 700; font-size: 16px; line-height: 1.35;
    display: flex; flex-direction: column; align-items: center; justify-content: center; text-align: center;
  }
  .bubble::after { content: ""; position: absolute; left: 50%; bottom: -7px; margin-left: -7px; border: 7px solid transparent; border-bottom: 0; border-top-color: var(--pink); }

  .tab {
    position: absolute; left: 122px; top: 0; width: 80px; height: 46px;
    background: var(--pink); border-radius: 0 0 8px 8px; color: var(--white);
    font-family: "Oswald", sans-serif; font-weight: 700; font-size: 15px;
    display: flex; align-items: center; justify-content: center;
  }
</style>
</head>
<body>
<main class="stage">

  <!-- Row 1: text-only set -->
  <section class="card col-1 row-1">
    <div class="frame">
      <span class="halo halo-tl"></span><span class="halo halo-br"></span>
      <div class="pill" style="left:14px;top:20px;width:187px;height:38px;font-size:23px;">TEN-WEEK</div>
      <div class="t wide" style="top:86px;font-size:31px;">BRIGHT</div>
      <div class="t wide" style="top:123px;font-size:28px;">MORNING</div>
      <div class="t script" style="top:168px;font-size:44px;">Reboot</div>
    </div>
  </section>

  <section class="card col-2 row-1">
    <div class="frame">
      <span class="halo halo-tl"></span><span class="halo halo-br"></span>
      <div class="t script" style="top:52px;font-size:28px;">Quick - Garden</div>
      <div class="t wide" style="top:92px;font-size:27px;">KITCHEN</div>
      <div class="t wide" style="top:122px;font-size:40px;">MENU</div>
      <div class="pill" style="left:7px;top:184px;width:204px;height:38px;font-size:21px;">GUIDE</div>
    </div>
  </section>

  <section class="card col-3 row-1">
    <div class="frame">
      <span class="halo halo-tl"></span><span class="halo halo-br"></span>
      <div class="bubble"><span>STUDIO HABITS</span><span>FOR LASTING</span></div>
      <div class="t wide" style="top:104px;font-size:38px;">ENERGY</div>
      <div class="t wide" style="top:152px;font-size:26px;">PAST</div>
      <div class="t script" style="top:188px;font-size:34px;color:var(--green);">Midlife</div>
      <div class="t lex" style="top:238px;font-weight:700;font-size:14px;color:var(--pink-deep);">ZERO GYM NEEDED</div>
    </div>
  </section>

  <!-- Row 2: single photo set -->
  <section class="card col-1 row-2">
    <div class="frame">
      <span class="halo halo-tl"></span><span class="halo halo-br"></span>
      <div class="t wide" style="top:20px;font-size:28px;">TEN-WEEK</div>
      <div class="pill" style="left:4px;top:58px;width:207px;height:35px;font-size:16px;">BRIGHT MORNING</div>
      <div class="t lex" style="top:103px;font-weight:700;font-size:22px;color:var(--green);">REBOOT</div>
      <div class="photo photo-person" role="img" aria-label="Smiling woman in a white cropped sweater pointing to her waist" style="left:52px;top:132px;width:112px;height:141px;"></div>
    </div>
  </section>

  <section class="card col-2 row-2">
    <div class="frame">
      <span class="halo halo-br"></span>
      <div class="photo photo-food fade-bottom" role="img" aria-label="Top-down table of chicken breast, fresh fruit, asparagus and a printed weekly menu sheet" style="left:0;top:0;width:215px;height:160px;"></div>
      <div class="t wide" style="top:161px;font-size:17px;">QUICK GARDEN</div>
      <div class="t round pink" style="top:185px;font-size:25px;">Kitchen Menu</div>
      <div class="pill round" style="left:9px;top:225px;width:193px;height:38px;font-size:27px;font-family:'Poppins',sans-serif;letter-spacing:0;">Guide</div>
    </div>
  </section>

  <section class="card col-3 row-2">
    <div class="frame">
      <span class="halo halo-br"></span>
      <div class="photo photo-friends fade-bottom" role="img" aria-label="Two women sharing a whispered secret, one looking delighted" style="left:0;top:0;width:215px;height:166px;"></div>
      <div class="t lex" style="top:159px;font-weight:600;font-size:15px;color:var(--green);">STUDIO HABITS</div>
      <div class="t lex" style="top:181px;font-weight:600;font-size:16px;color:var(--pink);">FOR LASTING ENERGY</div>
      <div class="t wide" style="top:208px;font-size:22px;letter-spacing:0;">PAST MIDLIFE</div>
      <div class="pill" style="left:8px;top:239px;width:202px;height:24px;font-size:13px;font-weight:600;">ZERO GYM NEEDED</div>
    </div>
  </section>

  <!-- Row 3: side photo set -->
  <section class="card col-1 row-3">
    <div class="frame">
      <span class="halo halo-tl"></span><span class="halo halo-br"></span>
      <div class="tab">TEN-WEEK</div>
      <div class="photo photo-person" role="img" aria-label="Smiling woman in a white cropped sweater pointing to her waist" style="left:0;top:49px;width:130px;height:224px;border-radius:60px 60px 0 0;"></div>
      <div class="t t-right lex" style="right:10px;top:64px;font-weight:600;font-size:22px;color:var(--green);">BRIGHT</div>
      <div class="t t-right lex" style="right:8px;top:96px;font-weight:600;font-size:18px;color:var(--green);">MORNING</div>
      <div class="t t-right cond pink" style="right:10px;top:160px;font-size:36px;">REBOOT</div>
    </div>
  </section>

  <section class="card col-2 row-3">
    <div class="frame">
      <div class="photo photo-food fade-mid" role="img" aria-label="Fresh tomatoes, bananas, greens, lentils, peppers and raw meat framing a wooden table" style="left:0;top:0;width:215px;height:273px;"></div>
      <div class="t lex" style="top:84px;font-weight:600;font-size:18px;color:var(--green);">QUICK GARDEN</div>
      <div class="t cond pink" style="top:114px;font-size:32px;">KITCHEN MENU</div>
      <div class="t wide" style="top:164px;font-size:30px;">GUIDE</div>
    </div>
  </section>

  <section class="card col-3 row-3">
    <div class="frame">
      <span class="halo halo-tl"></span>
      <div class="photo photo-friends" role="img" aria-label="Two women sharing a whispered secret, one looking surprised" style="left:116px;top:88px;width:99px;height:185px;border-radius:46px 0 0 0;"></div>
      <div class="t t-left wide" style="top:16px;font-size:24px;">STUDIO</div>
      <div class="t t-left lex" style="top:47px;font-weight:600;font-size:18px;color:var(--green);">HABITS FOR</div>
      <div class="t t-left lex" style="top:84px;font-weight:700;font-size:19px;color:var(--pink);">LASTING</div>
      <div class="t t-left lex" style="top:114px;font-weight:700;font-size:19px;color:var(--pink);">ENERGY</div>
      <div class="t t-left lex" style="top:150px;font-weight:600;font-size:17px;color:var(--green);">PAST</div>
      <div class="t t-left wide" style="top:176px;font-size:20px;letter-spacing:0;">MIDLIFE</div>
      <div class="pill" style="left:9px;top:238px;width:197px;height:20px;font-size:12px;font-weight:600;">ZERO GYM NEEDED</div>
    </div>
  </section>

</main>
</body>
</html>
```